Church Website with Home Page and Member Sermon Library

I am in need of an updated design for our church website. This will include 4 pages (outlined below). We are a conservative, evangelical, Christian church. The site should be modern and clean, while still reflecting our conservative values. I already have a logo for our church, and I want the site to incorporate the logo, and match the logo/branding. Stock photos are allowed if needed, but I have uploaded some images of our church and would prefer those images to be used if possible. Any stock photos used should not include any people in the photos (scenery, nature, buildings, animals, etc. are fine).

The site will need 4 pages: Home, Support Us (Donate), Login, and Recording Library.

Page 1: Home
The home page should include the following sections:

- Navigation: Should include links to each section of the home page plus a "listen live" link which will take the user to a live-streaming site and a "support us" link which will take the user to a support/donate page.

- Announcements: Can be either a banner or some other design, but there needs to be some way for us to post announcements for visitors to see. I'm open for creative ideas in this section, but would like it not to take up a lot of room on the page.

- About Us: Should include address, service times (see attached document), and information about the church.

- Pastor Bio: A section that introduces our pastor and gives a short bio about our pastor. Would like this section to include a picture of our pastor. Somewhere in this section I would like to include this Bible reference: "And I will give you pastors according to mine heart, which shall feed you with knowledge and understanding. Jer 3:15 LPW"

- Articles of Faith (What We Believe): This should include several sub-sections each with a heading, body, and possibly 1 or more scripture references. I have attached a document to the brief that includes our articles of faith. Feel free to be creative with this section in how you lay these out and format them.

- Support Us: A small section that explains what kind of support someone can give and a link to a donation page. The link can say something like "Support Us" or "Donate Now".

- Contact form: A contact form that allows the visitor to send us a message. The contact form should ask for name, email, phone, and message.

- Footer: A footer that will be displayed on all pages of the site. This should include at a minimum a link to the home page (or a link to each individual section in the home page if you prefer), a link to "listen live", a link to "support us", a link to "contact us" (or you can put the contact form directly in the footer if you prefer), the address, and a "member login" link.

Page 2: Support Us
The donation page should include a form the visitor can fill out to make a donation. We will embed a third party form later. For this design, please just mock out the design with a basic form asking for name, phone, and email.

Page 3: Login
The recording library (detailed below) will require members to login with a shared numeric code before accessing the page. We need a design for a login screen. The screen should include navigation/footer just like all other pages, but the body of the login page will consist only of a form that asks the user to enter the access code and then a "login" button.

Page 4: Recording Library

The library page is a member-only page that will require a shared, numeric pass code to access. On this page, members will be able to access a filterable list of past sermons. The page by default should display most recent sermons, but should also include a search form that allows the member to filter the sermon list to find a particular sermon. The search form should allow the user to select a filter type (e.g. Speaker name, date, event, etc.) and type in a value to search. They should be able to add multiple filters and remove filters that have been added. Each sermon that is displayed in the result list should include basic information such as title, date, speaker, tags, etc. along with a download icon, and an embedded audio player where they can click a play button to stream it on-demand. Each sermon should also have clickable tags associated with it that can be used to find related sermons.
Updates

I have uploaded several images of our church. Feel free to incorporate these into your design if possible.

Target Market(s)

Church Members

Industry/Entity Type

Religion

Number of Pages Required

4 page

Font styles to use
Sans Serif

Colors

Designer to choose colors to be used in the design.

Requirements
Must have
• Must incorporate the logo (attached)
Nice to have
• Would like the design to incorporate pictures of our church (attached) instead of stock photos if possible.
Should not have
• Please avoid an overly cluttered design. Stock photos used should not include any people in the photos.

```html
<!DOCTYPE html>
<html lang="en">
<head>
<meta charset="utf-8">
<title>Grace Valley Church</title>
<link href="https://fonts.googleapis.com/css2?family=Open+Sans:wght@300;400;600;700&family=Libre+Baskerville:wght@400;700&display=swap" rel="stylesheet">
<style>
:root{
  --green:#8aab6c;
  --green-dark:#6f8f55;
  --green-pale:#e3ebda;
  --teal:#12a5c9;
  --ink:#222;
  --text:#555;
  --muted:#888;
  --paper:#f7f8f4;
  --footer:#3b3b3b;
  --line:#ddd;
}
*{box-sizing:border-box;margin:0;padding:0}
html,body{width:1200px;height:3070px;overflow:hidden}
body{position:relative;font-family:"Open Sans",sans-serif;color:var(--text);background:#fff}
.abs{position:absolute}
.serif{font-family:"Libre Baskerville",serif}

/* header */
.site-header{left:0;top:0;width:1200px;height:81px;background:#f4f4f2}
.brand{display:flex;align-items:center;gap:8px;font-family:"Open Sans",sans-serif;font-weight:600;color:var(--green);font-size:15px;letter-spacing:1px;line-height:1.1}
.brand-mark{width:14px;height:14px;background:var(--green);flex:none}
.site-header .brand{left:150px;top:24px}
.main-nav{left:364px;top:34px;display:flex;gap:29px;font-size:11.5px;font-weight:600;letter-spacing:.3px;color:#333}
.pill-btn{display:flex;align-items:center;gap:5px;height:31px;border-radius:3px;color:#fff;font-size:11px;line-height:1;padding:0 6px}
.pill-btn.live{background:var(--green)}
.pill-btn.support{background:var(--teal)}
.pill-btn svg{flex:none}

/* hero */
.hero-photo{left:0;top:81px;width:1200px;height:470px;background:linear-gradient(100deg,#5b4134 0%,#8a5f4a 40%,#a07763 65%,#8e7b71 100%)}
.hero-shade{left:0;top:81px;width:1200px;height:470px;background:linear-gradient(90deg,rgba(30,20,15,.55),rgba(30,20,15,.05))}
.welcome-tag{left:0;top:170px;width:453px;height:52px;background:var(--green);border-radius:0 26px 26px 0;color:#fff;font-weight:600;font-size:20px;padding-left:181px;line-height:52px}
.hero-title{left:181px;top:236px;color:#fff;font-size:39px;font-weight:700}
.hero-copy{left:181px;top:302px;width:440px;border-left:2px solid var(--green);padding-left:12px;color:#fff;font-size:16.5px;line-height:21px}

/* announcements */
.announce{left:158px;top:471px;width:881px;height:173px;border-radius:86px 86px 0 0/86px 86px 0 0;background:rgba(248,248,246,.95);border-radius:90px}
.announce-label{left:248px;top:494px;color:var(--green);font-size:11px;letter-spacing:.5px}
.announce-title{left:246px;top:512px;color:#222;font-size:27px;font-weight:600}
.announce-body{left:247px;top:549px;width:480px;font-size:13.5px;line-height:19px;color:#999;font-weight:300}
.icon-circle{width:38px;height:38px;border-radius:50%;background:var(--green);display:flex;align-items:center;justify-content:center}
.slider-arrow{width:24px;height:24px;border-radius:50%;background:#444;display:flex;align-items:center;justify-content:center}

/* about */
.about-backdrop{left:149px;top:741px;width:392px;height:385px;background:#eef1ea}
.about-photo{left:161px;top:725px;width:380px;height:390px;background:linear-gradient(180deg,#cfd0cc 0%,#c4c3bd 40%,#9a7a63 60%,#b3ada4 78%,#9b9a95 100%)}
.about-badge{left:200px;top:1073px;width:302px;height:81px;background:var(--green);color:#fff;padding:7px 11px;line-height:31px}
.about-badge .l1{font-size:27px;font-weight:600;letter-spacing:.5px}
.about-badge .l2{font-size:21px;font-weight:400}
.about-copy{left:558px;top:729px;width:482px;font-size:14.6px;line-height:21px;color:#555}
.service-title{left:558px;top:923px;font-size:18px;font-weight:600;color:#222}
.service-lead{left:558px;top:952px;font-size:16px;color:#444}
.service-list{left:558px;top:981px;list-style:none;font-size:13px;color:#444}
.service-list li{display:flex;align-items:center;gap:7px;height:23px}
.about-rule{left:558px;top:1082px;width:424px;height:1px;background:var(--line)}
.address{left:558px;top:1091px;display:flex;gap:7px;align-items:center;font-size:13.5px;color:#444}

/* articles */
.section-title{left:0;width:1200px;text-align:center;color:#222;font-size:29px;font-weight:700}
.title-rule{left:561px;top:1266px;width:79px;height:3px;background:var(--green)}
.faith-card{left:158px;top:1298px;width:883px;height:236px;background:#fff;box-shadow:0 2px 6px rgba(0,0,0,.08)}
.faith-tabs{left:158px;top:1298px;width:883px;height:45px;background:#f2f2f2;display:flex;align-items:center;font-size:11.5px;font-weight:600;color:#333}
.faith-tabs .tab{height:45px;display:flex;align-items:center;padding:0 15px;line-height:15px}
.faith-tabs .tab.active{background:var(--teal);color:#fff;width:127px;justify-content:center}
.faith-heading{left:182px;top:1373px;font-size:21px;color:#222}
.faith-body{left:184px;top:1408px;width:830px;font-size:13.5px;line-height:19px;color:#333}
.faith-refs{left:184px;top:1453px;font-size:11.5px;color:var(--teal)}
.faith-refs span+span{border-left:1px solid #ccc;margin-left:6px;padding-left:7px}

/* live */
.live-photo{left:0;top:1567px;width:1200px;height:394px;background:linear-gradient(90deg,#3e3a36 0%,#6b564b 35%,#7a5e4e 60%,#55504c 100%)}
.live-shade{left:0;top:1567px;width:1200px;height:394px;background:rgba(40,35,32,.45)}
.live-title{left:0;top:1640px;width:1200px;text-align:center;color:#fff;font-size:27px;font-weight:700}
.live-copy{left:330px;top:1683px;width:540px;text-align:center;color:#fff;font-size:13.5px;line-height:25px}
.play-ring{left:546px;top:1781px;width:100px;height:100px}

/* support */
.support-band{left:163px;top:1912px;width:874px;height:221px;background:var(--green)}
.support-card{left:184px;top:1937px;width:201px;height:215px;background:#fff;overflow:hidden}
.support-card .arc{position:absolute;left:-50px;top:95px;width:170px;height:170px;border-radius:50%;background:var(--green-pale)}
.support-card .arc2{position:absolute;left:130px;top:-30px;width:140px;height:140px;border-radius:50%;background:#f2f5ee}
.support-card h3{position:absolute;left:0;top:72px;width:201px;text-align:center;font-size:27px;line-height:36px;color:#222}
.frame-tr{left:356px;top:1927px;width:38px;height:38px;border-top:4px solid #fff;border-right:4px solid #fff}
.frame-bl{left:176px;top:2120px;width:56px;height:40px;border-left:4px solid var(--green-dark);border-bottom:4px solid var(--green-dark)}
.support-title{left:408px;top:1932px;color:#fff;font-size:19px;font-weight:600}
.support-copy{left:408px;top:1966px;width:605px;color:#fff;font-size:12.7px;line-height:19px}
.goal-label{left:477px;top:2079px;color:#fff;font-size:9px;font-weight:600}
.goal-bar{left:408px;top:2098px;width:484px;height:5px;border-radius:3px;background:#fff}
.goal-fill{left:408px;top:2098px;width:83px;height:5px;border-radius:3px;background:var(--green-dark)}
.donate-btn{left:913px;top:2087px;width:86px;height:25px;background:#fff;color:#333;font-size:10px;display:flex;align-items:center;justify-content:center;border-radius:2px}

/* contact */
.footer-bg{left:0;top:2646px;width:1200px;height:424px;background:var(--footer)}
.contact-panel{left:150px;top:2216px;width:457px;height:521px;background:var(--paper)}
.contact-photo{left:607px;top:2216px;width:593px;height:521px;background:linear-gradient(180deg,#cfd0cd 0%,#c9c8c4 40%,#9c7c66 60%,#b5a998 80%,#aaa69e 100%)}
.contact-title{left:173px;top:2232px;font-size:25px;color:#333;font-weight:700}
.field-label{left:183px;font-size:15px;color:#999}
.field{left:181px;width:396px;background:#fff;border:1px solid #e6e6e6}
.submit-btn{left:181px;top:2672px;width:153px;height:41px;background:var(--green);color:#fff;font-size:16px;display:flex;align-items:center;justify-content:center;border-radius:2px}

/* footer */
.footer-brand{left:0;top:2855px;width:1200px;display:flex;justify-content:center}
.footer-brand .brand{font-size:20px}
.footer-nav{left:0;top:2908px;width:1200px;display:flex;justify-content:center;font-size:11.5px;font-weight:600;color:#fff;letter-spacing:.3px}
.footer-nav span{padding:0 14px}
.footer-nav span+span{border-left:1px solid #fff}
.copyright{left:0;top:3036px;width:1200px;text-align:center;color:#bbb;font-size:11px}
</style>
</head>
<body>

<header class="abs site-header">
  <div class="abs brand"><span class="brand-mark"></span><span>GRACE VALLEY<br>CHURCH</span></div>
  <nav class="abs main-nav"><span>HOME</span><span>ANNOUNCEMENTS</span><span>ABOUT US</span><span>PASTOR BIO</span><span>ARTICLES OF FAITH</span></nav>
  <a class="abs pill-btn live" style="left:874px;top:26px;width:70px">
    <svg width="20" height="20" viewBox="0 0 20 20" fill="none" stroke="#fff" stroke-width="1.8"><path d="M3 12V9a7 7 0 0 1 14 0v3"/><rect x="2" y="11" width="4" height="6" rx="1" fill="#fff"/><rect x="14" y="11" width="4" height="6" rx="1" fill="#fff"/></svg>
    <span>listen<br>live</span></a>
  <a class="abs pill-btn support" style="left:956px;top:26px;width:81px">
    <svg width="22" height="20" viewBox="0 0 22 20" fill="none" stroke="#fff" stroke-width="1.6"><path d="M11 17s-8-4.6-8-10a4 4 0 0 1 8-1 4 4 0 0 1 8 1c0 5.4-8 10-8 10z"/></svg>
    <span>Support<br>Us</span></a>
</header>

<section>
  <div class="abs hero-photo" role="img" aria-label="Photo of the brick church building with its front sign"></div>
  <div class="abs hero-shade"></div>
  <div class="abs welcome-tag">Welcome to Our Church</div>
  <h1 class="abs hero-title serif">JOIN THE PRAYER</h1>
  <p class="abs hero-copy">Become a part of Church and experience how the word of God changes lives. Feel free to join our church and the community that will help you on your way to discovering the power of Jesus Christ.</p>
</section>

<section>
  <div class="abs announce"></div>
  <div class="abs announce-label">ANNOUNCEMENTS</div>
  <h2 class="abs announce-title">BIBLE STUDY</h2>
  <p class="abs announce-body">Our church incorporates God's family into our fellowship. We provide a warm, authentic community, welcoming new believers into the body of Christ through baptism.</p>
  <div class="abs icon-circle" style="left:817px;top:537px"><svg width="18" height="14" viewBox="0 0 18 14"><rect x="0" y="0" width="18" height="14" rx="2" fill="#fff"/><path d="M7 4l5 3-5 3z" fill="#8aab6c"/></svg></div>
  <div class="abs icon-circle" style="left:863px;top:537px"><svg width="18" height="16" viewBox="0 0 18 16" stroke="#fff" stroke-width="1.6"><path d="M2 6v4M5 3v10M8 1v14M11 3v10M14 5v6M17 7v2"/></svg></div>
  <div class="abs icon-circle" style="left:908px;top:537px"><svg width="18" height="18" viewBox="0 0 18 18" fill="none" stroke="#fff" stroke-width="1.8"><path d="M9 2v10M5 8l4 4 4-4M2 16h14"/></svg></div>
  <div class="abs icon-circle" style="left:955px;top:537px"><svg width="16" height="20" viewBox="0 0 16 20" fill="none" stroke="#fff" stroke-width="1.6"><rect x="1" y="1" width="14" height="18" rx="2"/><path d="M4 6h8M4 10h8M4 14h5"/></svg></div>
  <div class="abs slider-arrow" style="left:927px;top:648px"><svg width="8" height="10" viewBox="0 0 8 10" fill="none" stroke="#fff" stroke-width="1.6"><path d="M6 1L2 5l4 4"/></svg></div>
  <div class="abs slider-arrow" style="left:954px;top:648px"><svg width="8" height="10" viewBox="0 0 8 10" fill="none" stroke="#fff" stroke-width="1.6"><path d="M2 1l4 4-4 4"/></svg></div>
</section>

<section>
  <div class="abs about-backdrop"></div>
  <div class="abs about-photo" role="img" aria-label="Photo of the church building and its parking lot under a grey sky"></div>
  <div class="abs about-badge"><div class="l1">WELCOME TO</div><div class="l2">GRACE VALLEY CHURCH</div></div>
  <p class="abs about-copy">Our church history began in December of 1995 with a small group of Christian believers that had a desire to serve God with their talent and gifts in a new ministry.&nbsp; In the beginning, services were held in the Harbor Ledger Offices on Linden Avenue in Millbrook and approximately 22 people were in attendance for the first Sunday morning worship service.&nbsp; About the second meeting, these believers held elections for church officers, teachers, and other levels of service to our Lord.&nbsp; At this time, another decision was made to name the new church,</p>
  <h3 class="abs service-title">Service Times</h3>
  <p class="abs service-lead">Feel free to customize the wording to match your design.</p>
  <ul class="abs service-list">
    <li><svg width="15" height="15" viewBox="0 0 16 16" fill="none" stroke="#333" stroke-width="1.4"><circle cx="8" cy="8" r="6.5"/><path d="M8 4v4l3 2"/></svg>Wednesday Evening Service: 7:30 PM</li>
    <li><svg width="15" height="15" viewBox="0 0 16 16" fill="none" stroke="#333" stroke-width="1.4"><circle cx="8" cy="8" r="6.5"/><path d="M8 4v4l3 2"/></svg>Sunday School: 10:00 AM</li>
    <li><svg width="15" height="15" viewBox="0 0 16 16" fill="none" stroke="#333" stroke-width="1.4"><circle cx="8" cy="8" r="6.5"/><path d="M8 4v4l3 2"/></svg>Sunday Morning Service: 11:00 AM</li>
    <li><svg width="15" height="15" viewBox="0 0 16 16" fill="none" stroke="#333" stroke-width="1.4"><circle cx="8" cy="8" r="6.5"/><path d="M8 4v4l3 2"/></svg>Sunday Evening Service: 5:30 PM</li>
  </ul>
  <div class="abs about-rule"></div>
  <div class="abs address"><svg width="15" height="17" viewBox="0 0 14 18" fill="none" stroke="#333" stroke-width="1.4"><path d="M7 17s6-6 6-10A6 6 0 0 0 1 7c0 4 6 10 6 10z"/><circle cx="7" cy="7" r="2.2"/></svg>1820 Meadowbrook Rd, Fairview, NC 27019, United States</div>
</section>

<section>
  <h2 class="abs section-title serif" style="top:1212px">ARTICLES OF FAITH</h2>
  <div class="abs title-rule"></div>
  <div class="abs faith-card"></div>
  <div class="abs faith-tabs">
    <div class="tab active">THE GOD HEAD</div>
    <div class="tab" style="width:118px">FULL SALVATION</div>
    <div class="tab" style="width:125px">SANCTIFICATION</div>
    <div class="tab" style="width:133px">BAPTISM OF<br>THE HOLY GHOST</div>
    <div class="tab">DIVINE HEALING</div>
  </div>
  <h3 class="abs faith-heading">THE GOD HEAD.</h3>
  <p class="abs faith-body">We believe in the God head bodily, known as the Divine Trinity. This body consist of God the father, Jesus Christ, his only begotten son and the redeemer of the world, and of the Holy Ghost, The third person of the Divine Trinity.</p>
  <div class="abs faith-refs"><span>References</span><span>References</span></div>
</section>

<section>
  <div class="abs live-photo" role="img" aria-label="Photo of the church front with its lanterns and sign"></div>
  <div class="abs live-shade"></div>
  <h2 class="abs live-title serif">A church that loves God and people</h2>
  <p class="abs live-copy">We believe that the Church is God's instrument for ministry here on Earth, and that makes it the greatest force on the face of the Earth. Click the below button to view live-streaming</p>
  <svg class="abs play-ring" viewBox="0 0 100 100" fill="none" stroke="#fff">
    <circle cx="50" cy="50" r="47" stroke-width="4"/>
    <circle cx="50" cy="50" r="40" stroke-width="2"/>
    <path d="M44 38l16 12-16 12z" fill="#fff" stroke="none"/>
    <path d="M32 36a20 20 0 0 0 0 28M24 30a28 28 0 0 0 0 40M68 36a20 20 0 0 1 0 28M76 30a28 28 0 0 1 0 40" stroke-width="4" stroke-linecap="round"/>
  </svg>
</section>

<section>
  <div class="abs support-band"></div>
  <div class="abs frame-bl"></div>
  <div class="abs support-card"><div class="arc2"></div><div class="arc"></div><h3 class="serif">SUPPORT<br>US</h3></div>
  <div class="abs frame-tr"></div>
  <h3 class="abs support-title">Your Contribution Matters</h3>
  <p class="abs support-copy">We would like to humbly request your support through donations. As a non-profit organization, we rely heavily on the generosity of people like you to help us continue our important work. Your donation will help us to provide assistance and resources to those in need, as well as to fund research and education initiatives. Every dollar counts and will make a difference in the lives of those we serve. Please consider making a donation and supporting our cause. <b>Thank you for your kindness and support.</b></p>
  <div class="abs goal-label">$1200</div>
  <div class="abs goal-bar"></div>
  <div class="abs goal-fill"></div>
  <a class="abs donate-btn">Donate Now</a>
</section>

<div class="abs footer-bg"></div>

<section>
  <div class="abs contact-panel"></div>
  <div class="abs contact-photo" role="img" aria-label="Photo of the church building seen from the parking lot"></div>
  <h2 class="abs contact-title serif">Contact Us</h2>
  <label class="abs field-label" style="top:2277px">Name</label>
  <div class="abs field" style="top:2306px;height:39px"></div>
  <label class="abs field-label" style="top:2352px">Email</label>
  <div class="abs field" style="top:2382px;height:38px"></div>
  <label class="abs field-label" style="top:2429px">Phone</label>
  <div class="abs field" style="top:2459px;height:38px"></div>
  <label class="abs field-label" style="top:2504px">Your Massage</label>
  <div class="abs field" style="top:2535px;height:120px"></div>
  <a class="abs submit-btn">GET IN TOUCH</a>
</section>

<footer>
  <div class="abs footer-brand"><div class="brand"><span class="brand-mark"></span><span>GRACE VALLEY CHURCH</span></div></div>
  <nav class="abs footer-nav"><span>HOME</span><span>ANNOUNCEMENTS</span><span>ABOUT US</span><span>PASTOR BIO</span><span>ARTICLES OF FAITH</span><span>CONTACT US</span></nav>
  <a class="abs pill-btn live" style="left:517px;top:2952px;width:71px">
    <svg width="20" height="20" viewBox="0 0 20 20" fill="none" stroke="#fff" stroke-width="1.8"><path d="M3 12V9a7 7 0 0 1 14 0v3"/><rect x="2" y="11" width="4" height="6" rx="1" fill="#fff"/><rect x="14" y="11" width="4" height="6" rx="1" fill="#fff"/></svg>
    <span>listen<br>live</span></a>
  <a class="abs pill-btn support" style="left:600px;top:2952px;width:81px">
    <svg width="22" height="20" viewBox="0 0 22 20" fill="none" stroke="#fff" stroke-width="1.6"><path d="M11 17s-8-4.6-8-10a4 4 0 0 1 8-1 4 4 0 0 1 8 1c0 5.4-8 10-8 10z"/></svg>
    <span>Support<br>Us</span></a>
  <p class="abs copyright">© 2023 Grace Valley Church. All rights reserved. Privacy Policy</p>
</footer>

</body>
</html>
```